Fast Growing Personal Injury Law Firm Needs Business Card Design

We need a business card design for a fast growing personal injury law firm in Florida. Our name is Dorian Kalvenfeld, P.A. Our practice is comprised of younger attorneys (in their 30s) that employ more modern techniques/tools than our older competition. We would prefer a look that is a modern play on a classic look. Also, we would like to continue using a color scheme that employs navy blue and kelly green (other shades of green could be fine too) as well as our "E" logo.

Industry/Entity Type

Law Firm

```html
<!DOCTYPE html>
<html lang="en">
<head>
<meta charset="utf-8">
<title>Dorian Kalvenfeld, P.A. — Business Card</title>
<link href="https://fonts.googleapis.com/css2?family=Crimson+Text:wght@400;600&family=Montserrat:wght@400;500&display=swap" rel="stylesheet">
<style>
  :root {
    --backdrop: #3b322d;
    --card-dark: #141618;
    --card-dark-edge: #23272b;
    --card-light: #f3f3f1;
    --sky-blue: #6cb8e4;
    --kelly-green: #7bbd2a;
    --icon-green: #2a9a3c;
    --ink: #1e1e1e;
    --ink-soft: #555555;
  }
  * { margin: 0; padding: 0; box-sizing: border-box; }
  html, body {
    width: 1200px; height: 768px; overflow: hidden;
    background: var(--backdrop);
  }
  .canvas {
    position: relative; width: 1200px; height: 768px;
  }
  .card {
    position: absolute; top: 236px;
    width: 520px; height: 296px;
    border-radius: 4px; overflow: hidden;
    box-shadow: 0 10px 24px rgba(0,0,0,.45);
  }
  .card--front {
    left: 50px;
    background: radial-gradient(circle at 55% 35%, var(--card-dark-edge), var(--card-dark) 70%);
  }
  .card--back { left: 630px; background: var(--card-dark); }

  .wordmark {
    display: flex; align-items: center; gap: 10px;
    font-family: "Crimson Text", serif; font-weight: 600;
    color: var(--sky-blue);
  }
  .wordmark__square {
    border: 2px solid var(--sky-blue);
  }
  .card--front .wordmark {
    position: absolute; left: 50%; top: 50%;
    transform: translate(-50%, -50%);
    font-size: 34px;
  }
  .card--front .wordmark__square { width: 26px; height: 26px; }

  .card__curve { position: absolute; inset: 0; }

  .firm {
    position: absolute; left: 22px; top: 62px; width: 200px;
    text-align: center;
  }
  .firm .wordmark {
    justify-content: center; font-size: 24px; margin-bottom: 18px;
  }
  .firm .wordmark__square { width: 18px; height: 18px; }
  .firm__name {
    font-family: "Crimson Text", serif; font-weight: 600;
    font-size: 19px; color: var(--sky-blue); line-height: 1.05;
  }
  .firm__tagline {
    font-family: "Crimson Text", serif; font-weight: 600;
    font-size: 16px; letter-spacing: .5px; color: var(--kelly-green);
  }

  .contact {
    position: absolute; left: 268px; top: 40px; width: 240px;
  }
  .contact__name {
    font-family: "Montserrat", sans-serif; font-weight: 500;
    font-size: 14px; letter-spacing: 2.5px; color: var(--ink);
  }
  .contact__role {
    font-family: "Montserrat", sans-serif; font-size: 11px;
    color: var(--ink-soft); margin-bottom: 38px;
  }
  .contact__address, .contact__list {
    font-family: "Crimson Text", serif; font-size: 14px;
    color: var(--ink); line-height: 1.25;
  }
  .contact__address { margin-bottom: 4px; }
  .contact__list { list-style: none; }
  .contact__list li { display: flex; align-items: center; gap: 7px; }
  .contact__list svg { width: 11px; height: 11px; flex: none; }
</style>
</head>
<body>
<main class="canvas">

  <section class="card card--front" aria-label="Card front">
    <div class="wordmark"><span class="wordmark__square"></span>Kalvenfeld</div>
  </section>

  <section class="card card--back" aria-label="Card back">
    <svg class="card__curve" viewBox="0 0 520 296" preserveAspectRatio="none" aria-hidden="true">
      <path d="M250 0 C200 90 205 210 110 296 L520 296 L520 0 Z" fill="#d9d9d7"/>
      <path d="M258 0 C212 92 218 212 124 296 L520 296 L520 0 Z" fill="var(--card-light)"/>
    </svg>

    <div class="firm">
      <div class="wordmark"><span class="wordmark__square"></span>Kalvenfeld</div>
      <p class="firm__name">Dorian Kalvenfeld, P.A.</p>
      <p class="firm__tagline">Personal Injury Attorneys</p>
    </div>

    <div class="contact">
      <p class="contact__name">DORIAN KALVENFELD</p>
      <p class="contact__role">Attorney at Law</p>
      <p class="contact__address">2215 Harborline Drive Suite 410<br>Palm Cove, Florida 34871</p>
      <ul class="contact__list">
        <li>
          <svg viewBox="0 0 12 12"><path d="M1 4 Q6 0 11 4 L9 5 L8 4 L4 4 L3 5 Z M3 6 L9 6 L10 11 L2 11 Z" fill="var(--icon-green)"/></svg>
          555 318 2740
        </li>
        <li>
          <svg viewBox="0 0 12 12"><rect x="3" y="1" width="6" height="4" fill="none" stroke="var(--icon-green)"/><rect x="1" y="5" width="10" height="6" rx="1" fill="var(--icon-green)"/></svg>
          555 318 2741
        </li>
        <li>
          <svg viewBox="0 0 12 12"><rect x="1" y="2.5" width="10" height="7" fill="var(--icon-green)"/><path d="M1 2.5 L6 7 L11 2.5" fill="none" stroke="#fff" stroke-width="1"/></svg>
          dorian@kalvenfeldlaw.com
        </li>
        <li>
          <svg viewBox="0 0 12 12"><circle cx="6" cy="6" r="5" fill="var(--icon-green)"/><path d="M1 6 H11 M6 1 V11 M6 1 Q3 6 6 11 M6 1 Q9 6 6 11" fill="none" stroke="#fff" stroke-width=".7"/></svg>
          www.kalvenfeldlaw.com
        </li>
      </ul>
    </div>
  </section>

</main>
</body>
</html>
```